Brightfield Ventures Inc. Letterhead

Creation of attractive and eye catching letterhead for a business start-up for the construction industry. Letterhead must relate to construction, but avoid standard hammer and tools in the design.

I forgot to add some details, sorry about that. Some pertinent info: Ph: 916-555-0187 brightfieldventures.example 448 Willowmere Ave, Ste 210 Folsom, CA 95999 info@brightfieldventures.example not sure if slogan should be in there" “Connecting construction professionals to create a purpose driven industry.” must be able to be used in word. Thanks!

```html
<!DOCTYPE html>
<html lang="en">
<head>
<meta charset="utf-8">
<title>Brightfield Ventures Inc. Letterhead</title>
<link href="https://fonts.googleapis.com/css2?family=Lato:wght@400;700&family=Montserrat:wght@600&family=Kaushan+Script&display=swap" rel="stylesheet">
<style>
  :root {
    --navy: #1d2456;
    --red: #c4262e;
    --body-text: #4a4a4a;
    --paper: #ffffff;
  }
  html, body {
    margin: 0;
    padding: 0;
    width: 906px;
    height: 1200px;
    overflow: hidden;
    background: var(--paper);
  }
  .letterhead {
    position: relative;
    width: 906px;
    height: 1200px;
    background: linear-gradient(180deg, #ffffff 0%, #f8f8fa 100%);
    font-family: "Lato", sans-serif;
  }
  .brand {
    position: absolute;
    top: 78px;
    left: 0;
    width: 100%;
    text-align: center;
  }
  .brand-mark {
    display: inline-block;
    width: 14px;
    height: 14px;
    background: var(--red);
    margin-bottom: 12px;
  }
  .brand-name {
    font-family: "Montserrat", sans-serif;
    font-weight: 600;
    font-size: 21px;
    letter-spacing: 2px;
    color: var(--navy);
    margin: 0;
    line-height: 1;
  }
  .brand-rule {
    width: 200px;
    height: 2px;
    background: var(--red);
    margin: 10px auto 0;
  }
  .letter {
    position: absolute;
    top: 230px;
    left: 77px;
    width: 753px;
    color: var(--body-text);
  }
  .salutation {
    font-weight: 700;
    font-size: 17px;
    color: var(--navy);
    margin: 0 0 20px;
  }
  .letter-body p {
    font-size: 17px;
    line-height: 28px;
    text-align: justify;
    margin: 0 0 20px;
  }
  .closing {
    font-size: 20px;
    color: #222;
    margin: 28px 0 0;
  }
  .signature {
    font-family: "Kaushan Script", cursive;
    font-size: 32px;
    color: var(--navy);
    margin: 6px 0 0;
  }
  .contact {
    position: absolute;
    top: 1138px;
    left: 0;
    width: 100%;
    text-align: center;
    font-size: 13px;
    color: #444;
  }
  .contact-line { margin: 0 0 8px; }
  .contact-item {
    display: inline-flex;
    align-items: center;
    gap: 4px;
    margin: 0 6px;
  }
  .contact-item svg { width: 11px; height: 11px; }
</style>
</head>
<body>
<main class="letterhead">
  <header class="brand">
    <span class="brand-mark"></span>
    <p class="brand-name">BRIGHTFIELD VENTURES</p>
    <div class="brand-rule"></div>
  </header>

  <section class="letter">
    <p class="salutation">Dear Mr. Lorem,</p>
    <div class="letter-body">
      <p>Lorem ipsum dolor sit amet, consectetuer adipiscing elit, sed diam nonummy nibh euismod tincidunt ut laoreet dolore magna aliquam erat volutpat. Ut wisi enim ad minim veniam, quis nostrud exerci tation ullamcorper suscipit lobortis nisl ut aliquip ex ea commodo consequat. Duis autem vel eum iriure dolor in hendiusto odio dignissim qui blandit praesent luptatum zzril delenit augue duis dolore te feugait nulla facilisi.</p>
      <p>Lorem ipsum dolor sit amet, consectetuer adipiscing elit, sed diam nonummy nibh euismod tincidunt ut laoreet dolore magna aliquam erat volutpat. Ut wisi enim ad minim veniam, quis nostrud exerci tation ullamcorper suscipit lobortis nisl ut aliquip ex ea commodo consequat. Duis autem vel eum iriure dolor in hendiusto odio dignissim qui blandit praesent luptatum zzril delenit augue duis dolore te feugait nulla facilisi.</p>
      <p>Lorem ipsum dolor sit amet, consectetuer adipiscing elit, sed diam nonummy nibh euismod tincidunt ut laoreet dolore magna aliquam erat volutpat. Ut wisi enim ad minim veniam, quis nostrud exerci tation ullamcorper suscipit lobortis nisl ut aliquip ex ea commodo consequat. Duis autem vel eum iriure dolor in hendiusto odio dignissim qui blandit praesent luptatum zzril delenit augue duis dolore te feugait nulla facilisi.</p>
    </div>
    <p class="closing">Sincerely Your,</p>
    <p class="signature">Your Name</p>
  </section>

  <footer class="contact">
    <p class="contact-line">
      <span class="contact-item">
        <svg viewBox="0 0 12 12" aria-hidden="true"><circle cx="6" cy="6" r="5" fill="none" stroke="#c4262e" stroke-width="1.4"/><circle cx="6" cy="5.5" r="1.8" fill="#c4262e"/></svg>
        448 Willowmere Ave, Ste 210, Folsom, CA 95999
      </span>
    </p>
    <p class="contact-line">
      <span class="contact-item">
        <svg viewBox="0 0 12 12" aria-hidden="true"><path d="M3 1.5l2 2.5-1.2 1.2c.6 1.3 1.7 2.4 3 3L8 7l2.5 2-1 1.5C5.5 10 2 6.5 1.5 2.5z" fill="#c4262e"/></svg>
        916-555-0187
      </span>
      <span class="contact-item">
        <svg viewBox="0 0 12 12" aria-hidden="true"><rect x="1" y="3" width="10" height="7" fill="#c4262e"/><path d="M1 3l5 4 5-4" fill="none" stroke="#fff" stroke-width="1"/></svg>
        info@brightfieldventures.example
      </span>
      <span class="contact-item">
        <svg viewBox="0 0 12 12" aria-hidden="true"><circle cx="6" cy="6" r="5" fill="#c4262e"/><path d="M1 6h10M6 1c-2 2.5-2 7.5 0 10M6 1c2 2.5 2 7.5 0 10" fill="none" stroke="#fff" stroke-width=".8"/></svg>
        www.brightfieldventures.example
      </span>
    </p>
  </footer>
</main>
</body>
</html>
```